Business Card for my New Brokerage

Looking to get a business card design for my new Real Estate Brokerage.
I want it with Picture, Phone Number, Email, Website, Office Address
Name and Designation. Please add logo too.

Target Market(s)

Real Estate Investors or Home Buyers

Industry/Entity Type

Real Estate

Contact Information for Business Card

Name, Email, Phone Number, website, email, office address

Colors
EB3D1F
EC4F4E
F09395
F8D3D4
FCEDEE

Requirements
Must have
• Minimalistic, Clean, Modern, Photo
Nice to have
• White and Red Colors

```html
<!DOCTYPE html>
<html lang="en">
<head>
<meta charset="utf-8">
<title>Lumen Realty Inc – Business Card</title>
<link href="https://fonts.googleapis.com/css2?family=Montserrat:wght@400;500;700&display=swap" rel="stylesheet">
<style>
  :root {
    --stage: #8b8d8f;
    --card-dark: #262626;
    --card-light: #ffffff;
    --brand-red: #e53a22;
    --ink: #2b2b2b;
    --mark-dark: #3a3a3a;
    --skyline: #ececec;
    --photo-light: #e6e6e6;
    --photo-dark: #6f6f6f;
  }
  * { margin: 0; padding: 0; box-sizing: border-box; }
  html, body { width: 1187px; height: 1200px; overflow: hidden; }
  body {
    position: relative;
    background: var(--stage);
    font-family: "Montserrat", sans-serif;
  }
  .card {
    position: absolute;
    border-radius: 16px;
    overflow: hidden;
  }
  .card--back {
    left: 218px; top: 122px; width: 752px; height: 430px;
    background: var(--card-dark);
  }
  .card--back .wordmark {
    position: absolute;
    left: 0; right: 0; top: 160px;
    text-align: center;
    color: var(--mark-dark);
    font-weight: 700;
  }
  .wordmark__name { display: block; font-size: 68px; letter-spacing: 1px; line-height: 1; }
  .wordmark__sub { display: block; font-size: 19px; letter-spacing: 7px; margin-top: 8px; }

  .card--front {
    left: 213px; top: 644px; width: 761px; height: 434px;
    background: var(--card-light);
  }
  .skyline {
    position: absolute;
    left: 0; top: 237px; width: 420px; height: 197px;
    background: linear-gradient(to bottom, rgba(236,236,236,0.3), var(--skyline));
  }
  .portrait {
    position: absolute;
    left: 417px; top: 29px; width: 344px; height: 405px;
    background: radial-gradient(ellipse at 52% 40%, var(--photo-light) 0%, #bdbdbd 45%, var(--photo-dark) 100%);
  }
  .card--front .wordmark {
    position: absolute;
    left: 46px; top: 52px;
    color: var(--brand-red);
    font-weight: 700;
  }
  .card--front .wordmark__name { font-size: 60px; }
  .card--front .wordmark__sub { font-size: 17px; letter-spacing: 5px; margin-top: 4px; padding-left: 48px; }

  .person { position: absolute; left: 46px; top: 188px; }
  .person__name { color: var(--brand-red); font-weight: 700; font-size: 29px; letter-spacing: 0.5px; line-height: 1.1; }
  .person__role { color: var(--ink); font-size: 17px; font-weight: 500; letter-spacing: 0.6px; margin-top: 4px; }
  .rule { width: 58px; height: 3px; background: var(--brand-red); margin: 7px 0 8px; }
  .address { color: var(--ink); font-size: 17px; font-weight: 500; letter-spacing: 0.6px; line-height: 27px; }
  .contacts { list-style: none; margin-top: 6px; }
  .contacts li {
    display: flex; align-items: center; gap: 7px;
    color: var(--ink); font-size: 17px; font-weight: 500; letter-spacing: 0.6px;
    height: 29px;
  }
  .contacts svg { width: 14px; height: 14px; flex: none; fill: var(--brand-red); }
</style>
</head>
<body>

  <section class="card card--back">
    <div class="wordmark">
      <span class="wordmark__name">LUMEN</span>
      <span class="wordmark__sub">REALTY INC</span>
    </div>
  </section>

  <section class="card card--front">
    <div class="skyline" role="img" aria-label="Faint city skyline silhouette"></div>
    <div class="portrait" role="img" aria-label="Black and white portrait of the broker associate"></div>

    <div class="wordmark">
      <span class="wordmark__name">LUMEN</span>
      <span class="wordmark__sub">REALTY INC</span>
    </div>

    <div class="person">
      <h1 class="person__name">CLAIRE MORTON</h1>
      <p class="person__role">Broker Associate</p>
      <div class="rule"></div>
      <p class="address">204 205, Harbor Point Complex<br>Riverside Business Park</p>
      <div class="rule"></div>
      <ul class="contacts">
        <li>
          <svg viewBox="0 0 24 24" aria-hidden="true"><path d="M6.6 10.8a15.1 15.1 0 0 0 6.6 6.6l2.2-2.2a1 1 0 0 1 1-.25 11.4 11.4 0 0 0 3.6.57 1 1 0 0 1 1 1V20a1 1 0 0 1-1 1A17 17 0 0 1 3 4a1 1 0 0 1 1-1h3.5a1 1 0 0 1 1 1c0 1.25.2 2.45.57 3.57a1 1 0 0 1-.25 1z"/></svg>
          555-014-2876
        </li>
        <li>
          <svg viewBox="0 0 24 24" aria-hidden="true"><path d="M2 5h20v14H2z M2 5l10 8 10-8" fill="var(--brand-red)"/><path d="M3 6l9 7 9-7" fill="none" stroke="#fff" stroke-width="1.6"/></svg>
          info@lumenrealtyinc.com
        </li>
        <li>
          <svg viewBox="0 0 24 24" aria-hidden="true"><circle cx="12" cy="12" r="10"/><path d="M2 12h20M12 2c3 3 3 17 0 20M12 2c-3 3-3 17 0 20M4 7h16M4 17h16" fill="none" stroke="#fff" stroke-width="1.3"/></svg>
          www.lumenrealtyinc.com
        </li>
      </ul>
    </div>
  </section>

</body>
</html>
```